K7 Electrical Services Ltd Web design

I require a web site for my new electrical contracting company. We are customer service orientated. Offering high value electrical installations, design and maintenance. Focused on custom residential and commercial upgrading. Lighting design and application are paramount in our company's services. Industry leading product use and integration are always on the forefront with our customer client services. As well as energy efficiency.

Target Market(s)

Homebuilders, General Contractors, Property management companies, clients, individuals,

Industry/Entity Type

Electric Company

Coding

Coded - Design and coding required

Number of Pages Required

3 page

Requirements
Must have
• Classic, modern, edgy but not trendy . Appeals to the masse.
• 3 page
• home page
• about page
• gallery page
• ability to contact from the webiste
Nice to have
• open to all types of designs that are relative to the construction industry.
• Black, Grey, metallic ice blue and deep purple colours from the logo.
Should not have
• anything cheesy with cartoon light bulb images.

```html
<!DOCTYPE html>
<html lang="en">
<head>
<meta charset="utf-8">
<title>K7 Electrical Services Ltd</title>
<link href="https://fonts.googleapis.com/css2?family=Montserrat:wght@400;500;600;700;800&family=Open+Sans:wght@400;600;700&display=swap" rel="stylesheet">
<style>
:root{
  --purple:#5e2b8c;
  --purple-dark:#4a1f70;
  --black:#111111;
  --ink:#1d1d1d;
  --dark:#222426;
  --grey:#6c6c6c;
  --light:#f4f4f6;
  --line:#e2e2e6;
  --white:#ffffff;
}
*{margin:0;padding:0;box-sizing:border-box}
html,body{width:1200px;height:4891px;overflow:hidden}
body{font-family:"Open Sans",Arial,sans-serif;color:var(--ink);background:var(--white);position:relative}
h1,h2,h3,h4,.heading{font-family:"Montserrat",Arial,sans-serif}
.abs{position:absolute}

/* top bar */
.topbar{position:absolute;left:0;top:0;width:1200px;height:108px;background:var(--black)}
.brand{position:absolute;left:0;top:0;width:412px;height:108px;background:var(--purple);clip-path:polygon(0 0,360px 0,412px 54px,360px 108px,0 108px);display:flex;align-items:center;padding-left:78px;gap:14px}
.brand-mark{width:34px;height:34px;border-radius:50%;background:var(--white)}
.brand-name{font-family:"Montserrat",sans-serif;font-weight:700;color:var(--white);font-size:20px;line-height:1.15;letter-spacing:1px;text-transform:uppercase}
.top-contact{position:absolute;top:28px;display:flex;gap:14px;align-items:flex-start;color:var(--white)}
.top-contact svg{margin-top:3px}
.top-contact b{display:block;font-size:14px;font-weight:600}
.top-contact span{font-size:13px;color:#cfcfcf}

/* nav */
.nav{position:absolute;left:0;top:108px;width:1200px;height:88px;background:var(--white);border-bottom:1px solid var(--line)}
.nav ul{list-style:none;display:flex;gap:44px;position:absolute;left:117px;top:46px}
.nav li{font-family:"Montserrat",sans-serif;font-size:14px;font-weight:600;color:var(--ink);text-transform:uppercase;position:relative}
.nav li.active{color:var(--purple)}
.nav li.active:after{content:"";position:absolute;left:0;right:0;bottom:-20px;height:4px;background:var(--purple)}
.social{position:absolute;right:40px;top:0;height:36px;display:flex;gap:16px;align-items:center;background:var(--purple);padding:0 20px;clip-path:polygon(24px 0,100% 0,100% 100%,0 100%)}
.social i{display:block;width:16px;height:16px;border-radius:50%;background:var(--white)}

/* hero */
.hero{position:absolute;left:0;top:196px;width:1200px;height:645px;background:linear-gradient(100deg,#3d3d42 0%,#6a6b70 45%,#a7a8ad 100%)}
.hero-shade{position:absolute;inset:0;background:linear-gradient(90deg,rgba(0,0,0,.55) 0%,rgba(0,0,0,.15) 60%,rgba(0,0,0,0) 100%)}
.hero-text{position:absolute;left:100px;top:196px;color:var(--white);width:520px}
.hero-text .eyebrow{font-size:18px;font-weight:600;margin-bottom:8px}
.hero-text h1{font-size:44px;font-weight:700;margin-bottom:14px}
.hero-text p{font-size:15px;line-height:1.6;margin-bottom:24px;color:#eee}
.btn{display:inline-block;font-family:"Montserrat",sans-serif;font-weight:700;font-size:12px;padding:13px 22px;text-transform:uppercase;color:var(--white)}
.btn.purple{background:var(--purple)}
.btn.dark{background:var(--black);margin-left:10px}

/* features */
.feature{position:absolute;top:906px;width:294px;height:170px;border:1px solid var(--line);background:var(--white);box-shadow:0 4px 14px rgba(0,0,0,.06)}
.feature .txt{position:absolute;left:18px;top:24px;width:180px}
.feature h3{font-size:15px;font-weight:700;margin-bottom:12px}
.feature p{font-size:11.5px;line-height:1.6;color:var(--grey)}
.feature .tab{position:absolute;right:0;top:0;width:84px;height:100%;background:var(--purple);clip-path:polygon(26px 0,100% 0,100% 100%,26px 100%,0 50%);display:flex;align-items:center;justify-content:center;padding-left:18px}

/* about */
.about-title{position:absolute;left:100px;top:1141px;font-size:34px;font-weight:700}
.about-lead{position:absolute;left:100px;top:1216px;width:520px;font-size:15px;line-height:1.6;font-weight:700}
.about-item{position:absolute;left:100px;width:520px;display:flex;gap:30px}
.about-item .ico{flex:none;width:72px;height:72px;border-radius:50%;background:var(--white);box-shadow:0 3px 14px rgba(0,0,0,.12);display:flex;align-items:center;justify-content:center}
.about-item h4{font-size:13px;font-weight:700;margin:8px 0 8px}
.about-item p{font-size:12px;line-height:1.65;color:var(--grey)}
.about-photo{position:absolute;left:650px;top:1141px;width:550px;height:554px;background:linear-gradient(135deg,#c9cdd8 0%,#7d8aa8 55%,#4e5a78 100%);clip-path:polygon(90px 0,100% 0,100% 100%,90px 100%,0 50%)}

/* services band */
.band{position:absolute;left:0;top:1780px;width:1200px;height:186px;background:var(--black);text-align:center;color:var(--white);padding-top:52px}
.section-title{font-size:34px;font-weight:700;text-transform:uppercase}
.section-sub{font-size:13px;margin-top:8px}

.tile{position:absolute;width:294px;height:195px;overflow:hidden}
.tile .photo{position:absolute;inset:0}
.tile .label{position:absolute;right:0;bottom:0;width:166px;height:44px;background:var(--purple);color:var(--white);font-family:"Montserrat",sans-serif;font-weight:700;font-size:14px;display:flex;align-items:center;justify-content:flex-end;padding-right:16px;clip-path:polygon(20px 0,100% 0,100% 100%,0 100%)}
.tile .hex{position:absolute;left:22px;bottom:12px}

/* gallery */
.services2-title{position:absolute;left:0;top:2528px;width:1200px;text-align:center}
.services2-title .section-sub{color:var(--grey)}
.tabs{position:absolute;left:278px;top:2634px;display:flex;height:34px}
.tabs span{font-family:"Montserrat",sans-serif;font-size:11px;font-weight:700;text-transform:uppercase;display:flex;align-items:center;padding:0 22px 0 26px;color:var(--white);background:var(--purple);clip-path:polygon(0 0,calc(100% - 12px) 0,100% 50%,calc(100% - 12px) 100%,0 100%,12px 50%)}
.tabs span.on{background:var(--white);color:var(--ink);border:1px solid var(--line);clip-path:none}
.gallery{position:absolute;left:0;top:2680px;width:1200px;height:390px;display:grid;grid-template-columns:repeat(4,300px);grid-template-rows:repeat(2,195px)}

/* testimonial */
.testi-head{position:absolute;left:0;top:3211px;width:1200px;text-align:center}
.testi-head .section-sub{color:var(--grey)}
.testi{position:absolute;top:3356px;width:420px;text-align:center}
.avatar{width:86px;height:86px;border-radius:50%;margin:0 auto 18px;background:linear-gradient(160deg,#b59a86,#6d5446);border:4px solid var(--white);box-shadow:0 2px 8px rgba(0,0,0,.15)}
.testi p{font-size:13px;line-height:1.6;color:var(--grey);position:relative}
.testi p:before{content:"\201C";position:absolute;left:-14px;top:-26px;font-size:80px;color:#e0e0e4;font-family:Georgia,serif}
.testi h4{color:var(--purple);font-size:20px;font-weight:700;margin-top:16px}
.testi small{font-size:13px;color:var(--grey)}
.dots{position:absolute;left:560px;top:3660px;display:flex;gap:9px}
.dots i{width:7px;height:7px;border-radius:50%;background:var(--ink)}

/* quote */
.quote-photo{position:absolute;left:0;top:3749px;width:640px;height:457px;background:linear-gradient(120deg,#d9d2c4 0%,#8c7a5e 45%,#2f4a7a 100%)}
.quote-panel{position:absolute;left:560px;top:3749px;width:640px;height:457px;background:#1c1c1f;clip-path:polygon(0 0,86% 0,100% 50%,86% 100%,0 100%)}
.quote-form{position:absolute;left:624px;top:3790px;width:410px;color:var(--white)}
.quote-form h2{font-size:30px;font-weight:700;margin-bottom:10px}
.quote-form p{font-size:11px;color:#b9b9b9;margin-bottom:18px;line-height:1.5}
.fields{display:grid;grid-template-columns:1fr 1fr;gap:10px}
.field{background:var(--white);height:38px;font-size:10px;color:#999;padding:8px 10px}
.field.area{grid-column:1/3;height:84px}
.send{margin-top:14px;display:inline-block;background:var(--purple);font-family:"Montserrat",sans-serif;font-weight:700;font-size:11px;padding:11px 16px;text-transform:uppercase}

/* partners */
.partners{position:absolute;left:100px;top:4225px;width:1000px;height:91px;display:grid;grid-template-columns:repeat(6,1fr);border:1px solid var(--line)}
.partners div{border-right:1px solid var(--line);display:flex;align-items:center;justify-content:center}
.partners div:last-child{border-right:none}
.partners i{display:block;width:70px;height:30px;border:2px solid #d6d6db;border-radius:4px}

/* footer */
.footer{position:absolute;left:0;top:4378px;width:1200px;height:513px;background:#1e1f22;color:var(--white)}
.f-brand{position:absolute;left:100px;top:110px;display:flex;align-items:center;gap:12px}
.f-brand .brand-mark{width:30px;height:30px}
.f-brand .brand-name{font-size:19px}
.f-about{position:absolute;left:100px;top:200px;width:290px;font-size:13px;line-height:1.6;color:#d0d0d0}
.f-col h3{font-size:20px;font-weight:700;margin-bottom:26px}
.f-links{display:flex;gap:60px}
.f-links ul{list-style:none}
.f-links li{font-size:13px;color:#cfcfcf;margin-bottom:9px;padding-left:16px;position:relative}
.f-links li:before{content:"";position:absolute;left:0;top:7px;width:5px;height:5px;border-radius:50%;background:var(--white)}
.f-contact{display:flex;gap:16px;align-items:flex-start;margin-bottom:18px;font-size:13px;color:#cfcfcf;line-height:1.5}
.f-contact .sq{flex:none;width:38px;height:38px;border:1px solid #5c5c62;display:flex;align-items:center;justify-content:center}
.f-social{position:absolute;left:0;top:382px;width:340px;height:52px;background:var(--purple);clip-path:polygon(0 0,300px 0,340px 26px,300px 52px,0 52px);display:flex;gap:28px;align-items:center;padding-left:100px}
.f-social i{display:block;width:18px;height:18px;border-radius:50%;background:var(--white)}
.copy{position:absolute;left:0;top:470px;width:1200px;text-align:center;font-size:13px;color:#cfcfcf}
</style>
</head>
<body>

<header class="topbar">
  <div class="brand"><span class="brand-mark"></span><span class="brand-name">K7 Electrical<br>Services</span></div>
  <div class="top-contact" style="left:660px">
    <svg width="20" height="20" viewBox="0 0 24 24" fill="#8b5cc4"><path d="M6.6 10.8a15 15 0 0 0 6.6 6.6l2.2-2.2c.3-.3.7-.4 1-.2 1.1.4 2.3.6 3.6.6.6 0 1 .4 1 1V20c0 .6-.4 1-1 1A17 17 0 0 1 3 4c0-.6.4-1 1-1h3.5c.6 0 1 .4 1 1 0 1.3.2 2.5.6 3.6.1.3 0 .7-.2 1z"/></svg>
    <div><b>Call Us Now</b><span>+61 1300 555 718</span></div>
  </div>
  <div class="top-contact" style="left:890px">
    <svg width="22" height="18" viewBox="0 0 24 18" fill="#8b5cc4"><path d="M0 0h24v18H0z" opacity=".0"/><path d="M2 0h20a2 2 0 0 1 2 2v14a2 2 0 0 1-2 2H2a2 2 0 0 1-2-2V2a2 2 0 0 1 2-2zm0 3v.5l10 6 10-6V3L12 9z"/></svg>
    <div><b>Send Mail Us</b><span>info@k7electrical.com</span></div>
  </div>
</header>

<nav class="nav">
  <div class="social"><i></i><i></i><i></i><i></i></div>
  <ul>
    <li class="active">Home</li><li>About Us</li><li>Features</li><li>Residential</li><li>Commercial</li><li>Reviews</li><li>Contact Us</li>
  </ul>
</nav>

<section class="hero" role="img" aria-label="Electrician in a blue cap working at an open electrical switchboard">
  <div class="hero-shade"></div>
  <div class="hero-text">
    <div class="eyebrow">K7 Electrical Services</div>
    <h1>Fast Electrical Services!</h1>
    <p>Universal business theme continues to grow - continues to grow every day thanks to the confidence our clients have in us.</p>
    <span class="btn purple">Our Company</span><span class="btn dark">Contact Us</span>
  </div>
</section>

<div class="feature" style="left:117px">
  <div class="txt"><h3>Professional HandyMan</h3><p>From network fixes to lighting upgrades, our trained team handles every job with care so you can relax.</p></div>
  <div class="tab"><svg width="34" height="34" viewBox="0 0 24 24" fill="none" stroke="#fff" stroke-width="1.6"><path d="M14 6l4-4 4 4-4 4zM3 21l9-9M7 3l3 3-2 2-3-3zM15 15l6 6"/></svg></div>
</div>
<div class="feature" style="left:453px">
  <div class="txt"><h3>24/7 Services</h3><p>If you are in an emergency situation, please do not worry. We provide 24/7 service whenever you call.</p></div>
  <div class="tab"><svg width="34" height="34" viewBox="0 0 24 24" fill="none" stroke="#fff" stroke-width="1.6"><circle cx="12" cy="12" r="9"/><path d="M12 7v5l3 2"/></svg></div>
</div>
<div class="feature" style="left:789px">
  <div class="txt"><h3>Affordable Price</h3><p>We do more than a handyman service: we check for faults that need attention so every job fits your needs.</p></div>
  <div class="tab"><svg width="36" height="30" viewBox="0 0 26 20" fill="none" stroke="#fff" stroke-width="1.6"><rect x="1" y="3" width="24" height="14"/><circle cx="13" cy="10" r="3"/></svg></div>
</div>

<h2 class="about-title">ABOUT US</h2>
<p class="about-lead">Lorem Ipsum is simply dummy text of the printing and typesetting industry. Lorem Ipsum has been the industry's standard dummy</p>
<div class="about-item" style="top:1320px">
  <div class="ico"><svg width="30" height="30" viewBox="0 0 24 24" fill="none" stroke="#5e2b8c" stroke-width="1.6"><circle cx="12" cy="12" r="9"/><text x="12" y="15" font-size="7" text-anchor="middle" fill="#5e2b8c" stroke="none" font-family="Montserrat">24</text></svg></div>
  <div><h4>SAVE TIME</h4><p>Our team of experts will assess your needs and develop a clear, custom installation plan tailored to your site and schedule.</p></div>
</div>
<div class="about-item" style="top:1440px">
  <div class="ico"><svg width="30" height="30" viewBox="0 0 24 24" fill="none" stroke="#5e2b8c" stroke-width="1.6"><path d="M4 20l6-6M14 4l6 6-6 6-6-6z"/></svg></div>
  <div><h4>SAVE EFFORT</h4><p>After identifying your needs, we will start upgrading your system. Your power and lighting will be ready in no time.</p></div>
</div>
<div class="about-item" style="top:1560px">
  <div class="ico"><svg width="30" height="24" viewBox="0 0 26 20" fill="none" stroke="#5e2b8c" stroke-width="1.6"><rect x="1" y="3" width="24" height="14"/><circle cx="13" cy="10" r="3"/></svg></div>
  <div><h4>SAVE MONEY</h4><p>Switching your home or office to efficient fittings cuts energy costs and lifts performance. You will see the difference.</p></div>
</div>
<div class="about-photo" role="img" aria-label="Electrician in blue overalls wiring a wall socket"></div>

<section class="band">
  <h2 class="section-title">Our Services</h2>
  <p class="section-sub">Lorem Ipsum is simply dummy text of the printing and typesetting</p>
</section>

<svg width="0" height="0" style="position:absolute"><defs><symbol id="hex" viewBox="0 0 56 48"><polygon points="14,0 42,0 56,24 42,48 14,48 0,24" fill="#111"/></symbol></defs></svg>

<div class="tile" style="left:117px;top:2005px"><div class="photo" role="img" aria-label="Worker renovating a room" style="background:linear-gradient(135deg,#e6ddd0,#a89276)"></div><svg class="hex" width="56" height="48"><use href="#hex"/></svg><div class="label">Renovation</div></div>
<div class="tile" style="left:453px;top:2005px"><div class="photo" role="img" aria-label="Electrician at a modern kitchen panel" style="background:linear-gradient(135deg,#d7d9dc,#5c6066)"></div><svg class="hex" width="56" height="48"><use href="#hex"/></svg><div class="label">Electrical</div></div>
<div class="tile" style="left:789px;top:2005px"><div class="photo" role="img" aria-label="Painter rolling paint on a wall" style="background:linear-gradient(135deg,#eef0f3,#8fa2bd)"></div><svg class="hex" width="56" height="48"><use href="#hex"/></svg><div class="label">Painting</div></div>
<div class="tile" style="left:117px;top:2215px"><div class="photo" role="img" aria-label="Plumber fixing pipes under a sink" style="background:linear-gradient(135deg,#f0f0f0,#7e8899)"></div><svg class="hex" width="56" height="48"><use href="#hex"/></svg><div class="label">Plumbing</div></div>
<div class="tile" style="left:453px;top:2215px"><div class="photo" role="img" aria-label="Technician drilling into a wall" style="background:linear-gradient(135deg,#bdbdbd,#3d3d3f)"></div><svg class="hex" width="56" height="48"><use href="#hex"/></svg><div class="label">Heating</div></div>
<div class="tile" style="left:789px;top:2215px"><div class="photo" role="img" aria-label="Roofer laying terracotta tiles" style="background:linear-gradient(135deg,#d98560,#8a3b24)"></div><svg class="hex" width="56" height="48"><use href="#hex"/></svg><div class="label">Roofing</div></div>

<div class="services2-title">
  <h2 class="section-title">Our Services</h2>
  <p class="section-sub">Lorem Ipsum is simply dummy text of the printing and typesetting</p>
</div>
<div class="tabs"><span class="on">Residential</span><span>Electrical</span><span>Interior</span><span>Painting</span><span>Plumbing</span><span>Repair</span></div>
<div class="gallery">
  <div role="img" aria-label="Technician at a window installation" style="background:linear-gradient(135deg,#e3e3e3,#8a8a8a)"></div>
  <div role="img" aria-label="Two tradespeople reviewing plans" style="background:linear-gradient(135deg,#c9d3a5,#6e7a4a)"></div>
  <div role="img" aria-label="Bright wooden interior hallway" style="background:linear-gradient(135deg,#e8d2a8,#a07a44)"></div>
  <div role="img" aria-label="Electrician working at a meter box" style="background:linear-gradient(135deg,#9a9a9a,#2e2e2e)"></div>
  <div role="img" aria-label="Woman drilling into a wall" style="background:linear-gradient(135deg,#e2dfe8,#8c8798)"></div>
  <div role="img" aria-label="Worker painting an outdoor wall" style="background:linear-gradient(135deg,#a6c27a,#4d6a33)"></div>
  <div role="img" aria-label="Builder cutting timber" style="background:linear-gradient(135deg,#a88660,#4f3a26)"></div>
  <div role="img" aria-label="Repairman servicing a washing machine" style="background:linear-gradient(135deg,#d3d3d6,#6e6e74)"></div>
</div>

<div class="testi-head">
  <h2 class="section-title">Testimonial</h2>
  <p class="section-sub">Lorem Ipsum is simply dummy text of the printing and typesetting</p>
</div>
<div class="testi" style="left:150px">
  <div class="avatar" role="img" aria-label="Customer portrait"></div>
  <p>Lorem ipsum dolor sit amet, consectetur adipiscing elit sed do eiusmod tempor incididunt ut labore et dolore magna aliqua. Ut enim ad minim veniam, quis nostrud exercitation ullamco laboris nisi.</p>
  <h4>Laura Bennett</h4><small>Customer</small>
</div>
<div class="testi" style="left:630px">
  <div class="avatar" role="img" aria-label="Customer portrait" style="background:linear-gradient(160deg,#a88d74,#5a4536)"></div>
  <p>Lorem ipsum dolor sit amet, consectetur adipiscing elit sed do eiusmod tempor incididunt ut labore et dolore magna aliqua. Ut enim ad minim veniam, quis nostrud exercitation ullamco laboris nisi.</p>
  <h4>Daniel Hart</h4><small>Customer</small>
</div>
<div class="dots"><i></i><i></i><i></i></div>

<div class="quote-photo" role="img" aria-label="Tradesman in gloves holding a cordless drill"></div>
<div class="quote-panel"></div>
<div class="quote-form">
  <h2>Get A Quick Quote</h2>
  <p>Send us an email by entering your details and any comments you may have in the form.</p>
  <div class="fields">
    <div class="field">First Name</div><div class="field">Your Email</div>
    <div class="field">Subject</div><div class="field">Phone</div>
    <div class="field area">Your Message</div>
  </div>
  <span class="send">Send Message</span>
</div>

<div class="partners"><div><i></i></div><div><i></i></div><div><i></i></div><div><i></i></div><div><i></i></div><div><i></i></div></div>

<footer class="footer">
  <div class="f-brand"><span class="brand-mark"></span><span class="brand-name">K7 Electrical<br>Services</span></div>
  <p class="f-about">Lorem ipsum dolor sit amet, lorem nibh lectus urna arcu, lorem erat semper, auctor suspendisse quisque molestie ut quisque molestie ut.</p>
  <div class="f-col abs" style="left:490px;top:90px">
    <h3>Useful Links</h3>
    <div class="f-links">
      <ul><li>About</li><li>Recruitment</li><li>Consulting</li><li>Development</li><li>Coaching</li></ul>
      <ul><li>Events</li><li>Blog</li><li>Contact</li></ul>
    </div>
  </div>
  <div class="f-col abs" style="left:800px;top:90px">
    <h3>Contact Us</h3>
    <div class="f-contact"><span class="sq"><svg width="16" height="18" viewBox="0 0 24 24" fill="#fff"><path d="M12 2a7 7 0 0 1 7 7c0 5-7 13-7 13S5 14 5 9a7 7 0 0 1 7-7zm0 4a3 3 0 1 0 0 6 3 3 0 0 0 0-6z"/></svg></span><span>Level 4, Suite 12 88 Harbour Road<br>Eastbank, Victoria 3010</span></div>
    <div class="f-contact"><span class="sq"><svg width="18" height="14" viewBox="0 0 24 18" fill="#fff"><path d="M2 0h20a2 2 0 0 1 2 2v14a2 2 0 0 1-2 2H2a2 2 0 0 1-2-2V2a2 2 0 0 1 2-2zm0 3v.5l10 6 10-6V3L12 9z"/></svg></span><span style="padding-top:9px">hello@k7electrical.com</span></div>
    <div class="f-contact"><span class="sq"><svg width="16" height="16" viewBox="0 0 24 24" fill="#fff"><path d="M6.6 10.8a15 15 0 0 0 6.6 6.6l2.2-2.2c.3-.3.7-.4 1-.2 1.1.4 2.3.6 3.6.6.6 0 1 .4 1 1V20c0 .6-.4 1-1 1A17 17 0 0 1 3 4c0-.6.4-1 1-1h3.5c.6 0 1 .4 1 1 0 1.3.2 2.5.6 3.6.1.3 0 .7-.2 1z"/></svg></span><span>+61 1300 555 718, +61 3 9604 2210<br>+61 (0) 412 300 981 (mob)</span></div>
  </div>
  <div class="f-social"><i></i><i></i><i></i><i></i></div>
  <p class="copy">© Copyright 2018 k7electricalservices.com | All Rights Reserved</p>
</footer>

</body>
</html>
```